Professional Photography Business cards

I need business cards that include my logo which I have uploaded. I run a photography business. I am open to ideas but I would like one side to have my logo and the other side to have my contact info. I don't have a website made but I do own a website domain. I have uploaded 2 different logo color schemes. My business colors are Blue, black , and white.

Business Name
Business Phone Number
Business Email
Business Website address
Instagram

Industry/Entity Type

Professional Photography

Contact Information for Business Card

Phone Number: 916-384-7702 email: info@tlane-studio.example Instagram: @t.lanestudio website doman- www.tlane-studio.example

Requirements
Must have
• I like the idea of a business card with a full black background front and back of card. My colors must include royal blue, black, and white

```html
<!DOCTYPE html>
<html lang="en">
<head>
<meta charset="utf-8">
<title>T. Lane Studio – Business Cards</title>
<link href="https://fonts.googleapis.com/css2?family=Open+Sans:wght@400;600&display=swap" rel="stylesheet">
<style>
  :root {
    --page-bg: #2a2a2a;
    --card-bg: #141414;
    --royal-blue: #2e35a8;
    --ink-white: #f4f4f4;
  }
  * { margin: 0; padding: 0; box-sizing: border-box; }
  html, body {
    width: 1200px; height: 900px; overflow: hidden;
    background: var(--page-bg);
    font-family: "Open Sans", Arial, sans-serif;
  }
  .sheet {
    width: 1200px; height: 900px;
    display: flex; flex-direction: column; align-items: center; justify-content: center;
    gap: 40px;
  }
  .card {
    width: 700px; height: 400px;
    background: var(--card-bg);
    border-radius: 4px;
    box-shadow: 0 10px 30px rgba(0,0,0,.5);
    display: flex; align-items: center;
    color: var(--ink-white);
  }
  .card--front { justify-content: center; }
  .brand { display: flex; align-items: center; gap: 18px; }
  .brand__dot {
    width: 54px; height: 54px; border-radius: 50%;
    border: 5px solid var(--ink-white);
  }
  .brand__name {
    font-weight: 600; font-size: 40px; letter-spacing: 1px;
    color: var(--ink-white);
  }
  .card--back { padding: 0 50px; gap: 34px; }
  .card--back .brand__dot { width: 38px; height: 38px; border-width: 4px; }
  .card--back .brand__name { font-size: 27px; }
  .divider {
    width: 2px; height: 150px; background: var(--royal-blue);
  }
  .contact { list-style: none; display: flex; flex-direction: column; gap: 10px; }
  .contact__item {
    display: flex; align-items: center; gap: 10px;
    font-size: 19px; color: var(--ink-white);
  }
  .contact__icon { width: 16px; height: 16px; flex: none; }
  .contact__icon--square {
    width: 13px; height: 13px; border: 2px solid var(--royal-blue); border-radius: 3px;
    margin: 0 1px;
  }
</style>
</head>
<body>
<main class="sheet">
  <section class="card card--front" aria-label="Card front">
    <div class="brand">
      <span class="brand__dot"></span>
      <span class="brand__name">T. Lane Studio</span>
    </div>
  </section>

  <section class="card card--back" aria-label="Card back">
    <div class="brand">
      <span class="brand__dot"></span>
      <span class="brand__name">T. Lane Studio</span>
    </div>
    <span class="divider"></span>
    <ul class="contact">
      <li class="contact__item">
        <svg class="contact__icon" viewBox="0 0 16 16" aria-hidden="true"><path fill="#2e35a8" d="M3.5 1l3 3-1.8 1.8a9 9 0 0 0 5.5 5.5L12 9.5l3 3-2 2C7 14 2 9 1.5 3z"/></svg>
        916-384-7702
      </li>
      <li class="contact__item">
        <svg class="contact__icon" viewBox="0 0 16 16" aria-hidden="true"><rect x="1" y="3" width="14" height="10" fill="#2e35a8"/><path d="M1 3l7 6 7-6" fill="none" stroke="#141414" stroke-width="1.5"/></svg>
        info@tlane-studio.example
      </li>
      <li class="contact__item">
        <svg class="contact__icon" viewBox="0 0 16 16" aria-hidden="true"><circle cx="8" cy="8" r="7" fill="#2e35a8"/><path d="M1 8h14M8 1c-3 3.5-3 10.5 0 14M8 1c3 3.5 3 10.5 0 14" fill="none" stroke="#141414" stroke-width="1"/></svg>
        www.tlane-studio.example
      </li>
      <li class="contact__item">
        <span class="contact__icon contact__icon--square"></span>
        @t.lanestudio
      </li>
    </ul>
  </section>
</main>
</body>
</html>
```